Sign for Pilates Studio

Cute and fun sandwich board sign ( 36" x 24" ) for outstanding Pilates studio in Santa Cruz. Sign should have logo, use the phrase "Pilates & Velmarique classes 7 Days a Week"
Updates

Dimensions are 36" x 24" and it should be clear and simple. The goal is to get people in the door. Try using the tree theme or the circle theme. Colors can be simple green, gold, burgundy....black lettering probably... Added Monday, January 12, 2015

Target Market(s)

Hip 30 year olds and everyone else too

Requirements
Must have
• It's a freestanding sign and should be simple to read
• Must say "Harbor Lantern Pilates"
• "Pilates Classes 7 days A week"
Nice to have
• Logo, tree. green and gold colors
Should not have
• Not too busy. Easy to read while driving by

```html
<!DOCTYPE html>
<html lang="en">
<head>
<meta charset="utf-8">
<title>Harbor Lantern Pilates – Sandwich Board Sign</title>
<link rel="stylesheet" href="https://fonts.googleapis.com/css2?family=Noto+Serif:ital,wght@0,400;1,400&family=Oxygen:wght@400&display=swap">
<style>
  :root {
    --backdrop: #b4b5b8;
    --sign-yellow: #ece22c;
    --brand-green: #16a44a;
    --ink: #111111;
    --soft-green: #c9dc3a;
  }
  * { margin: 0; padding: 0; box-sizing: border-box; }
  html, body { width: 1200px; height: 1000px; overflow: hidden; }
  body { background: var(--backdrop); position: relative; font-family: "Oxygen", sans-serif; }

  .sign {
    position: absolute; left: 296px; top: 45px; width: 608px; height: 910px;
    background: var(--sign-yellow);
  }

  .brand { position: absolute; left: 52px; top: 150px; width: 520px; }
  .brand-mark {
    position: absolute; left: 0; top: 10px; width: 46px; height: 46px;
    border-radius: 50%; background: var(--brand-green);
  }
  .brand-name {
    position: absolute; left: 60px; top: 0; white-space: nowrap;
    font-family: "Noto Serif", serif; font-size: 41px; color: var(--ink); line-height: 66px;
  }
  .brand-tagline {
    position: absolute; right: 0; top: 76px; white-space: nowrap;
    font-family: "Oxygen", sans-serif; font-size: 19px; color: var(--brand-green);
  }

  .headline {
    position: absolute; left: 0; width: 100%; top: 392px; text-align: center;
    font-family: "Noto Serif", serif; font-style: italic; font-size: 66px;
    color: var(--ink); line-height: 80px;
  }
  .subline {
    position: absolute; left: 0; width: 100%; top: 466px; text-align: center;
    font-family: "Oxygen", sans-serif; font-size: 64px; color: var(--brand-green);
    line-height: 74px;
  }

  .poses { position: absolute; left: 32px; top: 582px; width: 544px; height: 130px; }
  .pose {
    position: absolute; top: 0; width: 124px; height: 124px; border-radius: 50%;
    background: radial-gradient(circle, var(--soft-green) 0%, var(--brand-green) 100%);
    opacity: 0.55;
  }
  .pose--one { left: 2px; }
  .pose--two { left: 180px; }
  .pose--three { left: 360px; }

  .phone-band {
    position: absolute; left: 17px; top: 715px; width: 575px; height: 110px;
    border-radius: 10px; background: var(--brand-green);
    display: flex; align-items: center; justify-content: center;
    font-family: "Oxygen", sans-serif; font-size: 78px; color: var(--ink); letter-spacing: 1px;
  }
</style>
</head>
<body>
  <main class="sign">
    <div class="brand">
      <span class="brand-mark"></span>
      <span class="brand-name">Harbor Lantern Pilates</span>
      <span class="brand-tagline">Pilates &amp; Velmarique Studio</span>
    </div>

    <h1 class="headline">Pilates Classes</h1>
    <p class="subline">7 days a week</p>

    <div class="poses">
      <div class="pose pose--one" role="img" aria-label="Silhouette of a woman in a seated Pilates teaser pose inside a green swirl"></div>
      <div class="pose pose--two" role="img" aria-label="Silhouette of a woman in a Pilates rollover pose with legs raised inside a green swirl"></div>
      <div class="pose pose--three" role="img" aria-label="Silhouette of a woman in a side-lying Pilates leg lift inside a green swirl"></div>
    </div>

    <div class="phone-band">555 014 2290</div>
  </main>
</body>
</html>
```